UK based media owner TALMOX (http://www.talmox.uk/) needs DIGITAL ADVERT to run on our digital panel

Hi guys,

Thanks for taking the time to have a look at this brief.
I need someone to create a digital advert (still/static design or video) to run on our digital panels which are located across UK university student unions.
For who wants to upload a video ---> All of our panels are digitally enabled and allow for full motion video – they run adverts 10 seconds long (see artwork specification document in attachment) therefore the advert will have to be 10 seconds long.
For static/still design ----> see artwork specification to see resolution etc

I need something professional looking, polished yet fresh and exciting so that it speaks and connects to this younger audience – we want to inspire them to take a step towards new levels of business opportunities.

Here are some Key Points you’ll need to take into consideration when designing the advert:

Overall Campaign Objective: To excite and attract young entrepreneurs to get in touch with us for possible partnerships

Target Audience: Young entrepreneurs attending university (university students – 18 to 24 years old)

Creative Specifications: See attached document with artwork specifications

Text on Advert:

I need the following text to appear on the advert: (Please include company logo)

“Do you have a business idea that would benefit with advertising on these screens?

We want to support young entrepreneurs and will partner with any whom have a great idea

WE WANT TO HEAR FROM YOU!

Email us at ideas@talmox.uk
www.talmox.uk/ideas”

I would need some ideas by the 3rd July 2018 if possible.

Thanks to all who will take part in this project – contact me if you have any questions

Low designer entries

Need extra days to review

Target Market(s)

Young entrepreneurs attending university (university students – 18 to 24 years old)

Requirements
Must have
• I need the following text to appear on the advert: (Please include company logo)
• “Do you have a business idea that would benefit with advertising on these screens?
• We want to support young entrepreneurs and will partner with any whom have a great idea
• WE WANT TO HEAR FROM YOU!
• Email us at ideas@talmox.uk
• www.talmox.uk/ideas”

```html
<!DOCTYPE html>
<html lang="en">
<head>
<meta charset="utf-8">
<title>TALMOX – Business Ideas</title>
<link href="https://fonts.googleapis.com/css2?family=Lato:wght@300;400;700&display=swap" rel="stylesheet">
<style>
  :root {
    --paper: #efefef;
    --panel-grey: #dadada;
    --corner-grey: #e6e6e6;
    --brand-red: #b50f22;
    --ink: #111111;
    --url-ink: #222222;
    --white: #ffffff;
  }
  html, body {
    margin: 0;
    padding: 0;
    width: 675px;
    height: 1200px;
    overflow: hidden;
    background: var(--paper);
  }
  .advert {
    display: block;
    width: 675px;
    height: 1200px;
    font-family: 'Lato', sans-serif;
  }
  .bg-paper { fill: var(--paper); }
  .panel-grey { fill: var(--panel-grey); }
  .corner-grey { fill: var(--corner-grey); }
  .panel-red { fill: var(--brand-red); }
  .photo-fade { opacity: 0.35; }
  .headline-plain {
    font-weight: 300;
    font-size: 66px;
    fill: var(--ink);
  }
  .headline-accent {
    font-weight: 300;
    font-size: 82px;
    fill: var(--brand-red);
  }
  .headline-close {
    font-weight: 300;
    font-size: 88px;
    fill: var(--brand-red);
  }
  .support-copy {
    font-weight: 400;
    font-size: 20px;
    fill: var(--ink);
  }
  .call-out {
    font-weight: 700;
    font-size: 24px;
    fill: var(--brand-red);
  }
  .email-line {
    font-weight: 400;
    font-size: 22px;
    fill: var(--url-ink);
  }
  .brand-name {
    font-weight: 400;
    font-size: 46px;
    letter-spacing: 17px;
    fill: var(--white);
  }
  .web-address {
    font-weight: 400;
    font-size: 28px;
    letter-spacing: 0.5px;
    fill: var(--url-ink);
  }
</style>
</head>
<body>
<svg class="advert" viewBox="0 0 844 1500" width="675" height="1200" xmlns="http://www.w3.org/2000/svg">
  <defs>
    <linearGradient id="officeTone" x1="0" y1="0" x2="1" y2="1">
      <stop offset="0" stop-color="#d9d9d9"/>
      <stop offset="0.35" stop-color="#6f6a66"/>
      <stop offset="0.6" stop-color="#8a8a8a"/>
      <stop offset="1" stop-color="#d4d4d4"/>
    </linearGradient>
  </defs>

  <rect class="bg-paper" x="0" y="0" width="844" height="1500"/>

  <g role="img" aria-label="Blurred photo of a young man on the phone leaning on a desk in a bright office">
    <polygon points="110,0 844,0 844,400 545,645 265,310" fill="url(#officeTone)"/>
    <polygon class="photo-fade" points="545,645 844,400 844,1000" fill="url(#officeTone)"/>
  </g>

  <polygon class="panel-grey" points="0,0 110,0 265,310 545,645 100,1020 0,905"/>
  <polygon class="corner-grey" points="0,0 110,0 0,70"/>
  <polygon class="panel-red" points="0,905 470,1500 0,1500"/>

  <text class="headline-plain" x="62" y="558">Do you have</text>
  <text class="headline-accent" x="60" y="722">A BUSINESS IDEA</text>
  <text class="headline-plain" x="62" y="868">that would benefit</text>
  <text class="headline-plain" x="62" y="955">with advertising</text>
  <text class="headline-close" x="782" y="1118" text-anchor="end">ON THESE</text>
  <text class="headline-close" x="782" y="1228" text-anchor="end">SCREENS?</text>

  <text class="support-copy" x="782" y="1274" text-anchor="end">We want to support young entrepreneurs and</text>
  <text class="support-copy" x="782" y="1300" text-anchor="end">will partner with any whom have a great idea</text>
  <text class="call-out" x="782" y="1342" text-anchor="end">WE WANT TO HEAR FROM YOU!</text>
  <text class="email-line" x="782" y="1380" text-anchor="end">Email us at ideas@talmox.uk</text>

  <text class="brand-name" x="62" y="1437">TALMOX</text>
  <text class="web-address" x="784" y="1442" text-anchor="end">www.talmox.uk/ideas</text>
</svg>
</body>
</html>
```